Residential Remodeling Contractor needs updated business card

I need a new design for my business card.
Name of the company is Ridgefell Construction. I need a card that commands presence, strength, integrity. I have been in business for 28 years. I am a Residential Remodeling Contractor that covers all aspects of a residential remodel and build.

```html
<!DOCTYPE html>
<html lang="en">
<head>
<meta charset="utf-8">
<title>Ridgefell Construction – Business Card</title>
<link href="https://fonts.googleapis.com/css2?family=Montserrat:wght@400;700&display=swap" rel="stylesheet">
<style>
  :root {
    --backdrop: #d9d9d7;
    --card-blue: #1f3b7a;
    --card-blue-deep: #142a5c;
    --ink-light: #ffffff;
    --rule: rgba(255, 255, 255, 0.85);
  }
  * { box-sizing: border-box; margin: 0; padding: 0; }
  html, body {
    width: 1200px;
    height: 801px;
    overflow: hidden;
    background: var(--backdrop);
    font-family: "Montserrat", sans-serif;
  }
  .stage {
    position: relative;
    width: 1200px;
    height: 801px;
  }
  .card {
    position: absolute;
    top: 252px;
    width: 520px;
    height: 297px;
    background: var(--card-blue);
    color: var(--ink-light);
    box-shadow: 0 2px 6px rgba(0, 0, 0, 0.18);
  }
  .card--front { left: 50px; }
  .card--back { left: 630px; }

  /* Front */
  .brand {
    position: absolute;
    display: flex;
    align-items: center;
    gap: 10px;
    font-weight: 700;
    text-transform: uppercase;
    letter-spacing: 0.06em;
    line-height: 1.1;
  }
  .brand__square {
    flex: none;
    background: currentColor;
  }
  .card--front .brand {
    top: 46px;
    left: 250px;
    font-size: 19px;
  }
  .card--front .brand__square { width: 14px; height: 14px; }

  .person {
    position: absolute;
    left: 40px;
    top: 140px;
  }
  .person__name {
    font-weight: 700;
    font-size: 20px;
    letter-spacing: 0.03em;
    text-transform: uppercase;
  }
  .person__role {
    font-size: 11px;
    margin-top: 3px;
  }
  .divider {
    position: absolute;
    left: 40px;
    top: 190px;
    width: 250px;
    height: 1px;
    background: var(--rule);
  }
  .contacts {
    position: absolute;
    left: 40px;
    top: 200px;
    list-style: none;
    font-size: 12px;
    line-height: 17px;
  }
  .contacts li {
    display: flex;
    align-items: center;
    gap: 6px;
  }
  .contacts svg {
    width: 10px;
    height: 10px;
    flex: none;
  }
  .contacts .address { padding-left: 16px; }

  /* Back */
  .card--back .brand {
    top: 112px;
    left: 90px;
    font-size: 30px;
    color: var(--card-blue-deep);
  }
  .card--back .brand__square { width: 22px; height: 22px; }
  .tagline {
    position: absolute;
    right: 30px;
    bottom: 42px;
    font-size: 11px;
    font-weight: 700;
    letter-spacing: 0.04em;
    text-transform: uppercase;
  }
</style>
</head>
<body>
<main class="stage">
  <section class="card card--front">
    <div class="brand">
      <span class="brand__square"></span>
      <span>Ridgefell<br>Construction</span>
    </div>

    <div class="person">
      <p class="person__name">Marcus Delvane</p>
      <p class="person__role">Director</p>
    </div>

    <div class="divider"></div>

    <ul class="contacts">
      <li>
        <svg viewBox="0 0 10 10" aria-hidden="true"><path d="M2 1 L4 1 L4.6 3 L3.4 3.8 Q4.4 5.8 6.2 6.6 L7 5.4 L9 6 L9 8 Q9 9 8 9 Q1 8 1 2 Q1 1 2 1 Z" fill="#fff"/></svg>
        <span>(555) 014-2287</span>
      </li>
      <li>
        <svg viewBox="0 0 10 10" aria-hidden="true"><rect x="0.8" y="2" width="8.4" height="6" fill="none" stroke="#fff" stroke-width="1"/><path d="M0.8 2 L5 5.4 L9.2 2" fill="none" stroke="#fff" stroke-width="1"/></svg>
        <span>info@ridgefellbuild.com</span>
      </li>
      <li>
        <svg viewBox="0 0 10 10" aria-hidden="true"><circle cx="5" cy="5" r="4.2" fill="none" stroke="#fff" stroke-width="1"/><ellipse cx="5" cy="5" rx="1.8" ry="4.2" fill="none" stroke="#fff" stroke-width="0.8"/><line x1="0.8" y1="5" x2="9.2" y2="5" stroke="#fff" stroke-width="0.8"/></svg>
        <span>www.ridgefellbuild.com</span>
      </li>
      <li class="address">482 Alder Lane Millbrook, GA 30999</li>
    </ul>
  </section>

  <section class="card card--back">
    <div class="brand">
      <span class="brand__square"></span>
      <span>Ridgefell<br>Construction</span>
    </div>
    <p class="tagline">I have been in business for 28 years</p>
  </section>
</main>
</body>
</html>
```